Ad-Services Website

The project is for an agency which provides a 360 service around the world of printing and advertising. Without much focus on the advertising per say, but much more focus on the medium on which advertisement can be achieved, such as banners, moving banners, boards and so on.

Futhermore more the company deals with material printing so it has advertising agencies as clients.

Finally it represents several companies in Greece for materials around advertising such as stands, ad-walls, banners and so on.

The webpage needs to have web 2.0 look an feel, and it will lack in content, therefore the focus should not be in large sections of text.

I can have a pdf sent with a small presentation that was done to the client, and the structure to which he agreed to

The following website has the look & feel of what we are looking for

http://www.lumtaro.gr

The companies current website where you can get the colors and logos from is

http://korvibelt.gr
Updates

Hello,

Thank you all very much for your designs, we really appreciate your contribution.

Maybe in our next project we can work together.

Best Regards,
Manos

Industry/Entity Type

Advertising

```html
<!DOCTYPE html>
<html lang="en">
<head>
<meta charset="utf-8">
<title>Ad Services</title>
<link href="https://fonts.googleapis.com/css2?family=Arimo&display=swap" rel="stylesheet">
<style>
  :root {
    --sky-top: #d3dae4;
    --sky-mid: #e4e8ee;
    --horizon: #ffffff;
    --floor: #eceef2;
    --hub-top: #ffffff;
    --hub-bottom: #b8c5d3;
    --ring: #ffffff;
    --btn-grey-top: #7a7a7a;
    --btn-grey-bottom: #d2d2d2;
    --btn-cyan-top: #05313d;
    --btn-cyan-bottom: #3ae0f4;
    --btn-edge: #5b5b5b;
    --label: #ffffff;
    --mark-dark: #1a1a1a;
  }
  * { margin: 0; padding: 0; box-sizing: border-box; }
  html, body { width: 1200px; height: 506px; overflow: hidden; }
  body {
    font-family: "Arimo", Arial, sans-serif;
    position: relative;
    background:
      radial-gradient(ellipse 420px 170px at 600px 300px, var(--horizon) 0%, rgba(255,255,255,0) 100%),
      linear-gradient(to bottom, var(--sky-top) 0%, var(--sky-mid) 45%, var(--horizon) 58%, var(--floor) 100%);
  }
  .cloud-band {
    position: absolute;
    left: 230px; top: 0;
    width: 760px; height: 180px;
    background: radial-gradient(ellipse 380px 90px at 50% 45%, rgba(255,255,255,0.85) 0%, rgba(255,255,255,0.35) 55%, rgba(255,255,255,0) 100%);
  }
  .hub {
    position: absolute;
    left: 441px; top: 85px;
    width: 320px; height: 320px;
    border-radius: 50%;
    border: 3px solid var(--ring);
    background: linear-gradient(to bottom, var(--hub-top) 0%, #eef1f5 40%, var(--hub-bottom) 100%);
  }
  .hub-mark {
    position: absolute;
    left: 516px; top: 180px;
    width: 190px; height: 120px;
    border-radius: 60px 20px 60px 20px;
    background: radial-gradient(ellipse at 30% 70%, var(--mark-dark) 0%, rgba(26,26,26,0.25) 60%, rgba(26,26,26,0) 100%);
  }
  .service {
    position: absolute;
    width: 106px; height: 106px;
    border-radius: 50%;
    background: var(--ring);
    box-shadow: 0 0 4px rgba(120,130,145,0.35);
    display: flex; align-items: center; justify-content: center;
    text-decoration: none;
  }
  .service-face {
    width: 96px; height: 96px;
    border-radius: 50%;
    border: 1px solid var(--btn-edge);
    background: linear-gradient(to bottom, var(--btn-grey-top), var(--btn-grey-bottom));
    display: flex; align-items: center; justify-content: center;
    color: var(--label);
    font-size: 11px;
    text-shadow: 0 1px 1px rgba(0,0,0,0.55);
  }
  .service-active .service-face {
    border-color: #0a4a58;
    background: linear-gradient(to bottom, var(--btn-cyan-top), var(--btn-cyan-bottom));
  }
  .service-advertising { left: 417px; top: 117px; }
  .service-print { left: 709px; top: 185px; }
  .service-display { left: 552px; top: 341px; }
</style>
</head>
<body>
  <div class="cloud-band" role="img" aria-label="Soft white clouds across the sky"></div>
  <div class="hub"></div>
  <div class="hub-mark" role="img" aria-label="Central black swimming-shape illustration"></div>
  <nav>
    <a class="service service-advertising" href="#advertising"><span class="service-face">Advertisting</span></a>
    <a class="service service-print" href="#print"><span class="service-face">Print</span></a>
    <a class="service service-display service-active" href="#display"><span class="service-face">Display</span></a>
  </nav>
</body>
</html>
```